Paul Denton Sausage Label Design

Halvern Fields Corporation is seeking to create a new brand of fresh 100% Canadian pork sausage. This label will be a paper band that slips on and off foam trays. The front facing side will be 5 inches wide by 3.5 inches high. The following is some information about our brand.
Target market:
1. Working Moms
2. Stay at home moms
3. Barbeque enthusiast
Brand personality
1. Old school values – We are a family run company who believes in an honest days work
2. Modern day sensibility – We believe in being nimble and open to new ideas
3. Energetic and optimistic – We are passionate about our business and product
4. Relaxed sense of humor – We believe that it is possible to work hard and have fun
Positioning Statements:
Our sausage is the easy choice for adding flavour to your real- life family meals, that’s because:
1. It is 100% fresh Canadian product with no fillers or preservatives
2. It is a great tasting recipe with simple, natural ingredients
3. It is brought to you with good humor and integrity by a multi- generational family owned business
We are looking for a creative designer to make our ideas come to life. There are three types of designs we would like to see:
1. Rustic – a rustic, barbequing, old farm, country feel – without feeling too old
2. Modern & Simple – Very simple clean face with clean text
3. Family friendly – a label that would appeal to the everyday family with photos of the finished product
This brand does not have a name yet, please use the name “Paul Denton “as a place holder. Please keep in mind the information provided about our brand when developing the label. Attached are pictures of some ideas we like. Please do not copy these ideas too closely, we are looking to differentiate ourselves in the market. Samples are to provide some guidance of our preferences.
Target Market(s)
1. Working Moms
2. Stay at home moms
3. Barbeque enthusiast
Colors
Designer to choose colors to be used in the design.

```html
<!DOCTYPE html>
<html lang="en">
<head>
<meta charset="utf-8">
<title>Paul Denton – Mutton &amp; Mint Sausage Label</title>
<link rel="stylesheet" href="https://fonts.googleapis.com/css2?family=Alfa+Slab+One&family=Arvo:wght@700&family=Roboto+Slab:wght@900&family=Yellowtail&display=swap">
<style>
  :root {
    --label-blue: #4670b8;
    --cream: #eeeedf;
    --navy: #1c1040;
    --rule: 4px;
  }
  * { margin: 0; padding: 0; box-sizing: border-box; }
  html, body { width: 1200px; height: 843px; overflow: hidden; background: var(--label-blue); }
  .label {
    position: relative;
    width: 1200px;
    height: 843px;
    background: var(--label-blue);
    color: var(--cream);
    font-family: "Arvo", "Rockwell", serif;
    font-weight: 700;
  }
  .rule { position: absolute; background: var(--cream); }
  .rule--h { height: var(--rule); }
  .rule--v { width: var(--rule); }

  .text { position: absolute; line-height: 1; white-space: nowrap; }

  .company { left: 51px; top: 75px; font-size: 24px; letter-spacing: 0.3px; }

  .brand-name {
    position: absolute;
    left: 38px;
    top: 176px;
    font-family: "Roboto Slab", "Rockwell", serif;
    font-weight: 900;
    font-size: 112px;
    line-height: 108px;
    letter-spacing: -2px;
    color: var(--cream);
    text-shadow: 5px 5px 0 var(--navy);
    white-space: nowrap;
  }
  .brand-name span { display: block; }

  .hero-art {
    position: absolute;
    left: 578px; top: 22px; width: 535px; height: 362px;
    border-radius: 180px / 120px;
    background: radial-gradient(ellipse at 55% 60%, var(--cream) 0%, #b8bcc9 40%, var(--navy) 78%);
  }
  .map-art {
    position: absolute;
    left: 64px; top: 520px; width: 176px; height: 148px;
    border-radius: 14px;
    background: linear-gradient(160deg, var(--cream), #d9dccf);
  }

  .script { font-family: "Yellowtail", "Brush Script MT", cursive; font-weight: 400; }
  .origin { left: 254px; top: 478px; font-size: 31px; line-height: 0.95; transform: rotate(-3deg); }
  .natural { left: 428px; top: 476px; font-size: 40px; }

  .flavour { left: 430px; top: 562px; font-family: "Alfa Slab One", "Rockwell", serif; font-weight: 400; font-size: 59px; color: var(--navy); letter-spacing: 0.5px; }
  .product { left: 440px; top: 634px; font-size: 29px; }

  .count { left: 72px; top: 727px; font-size: 26px; }
  .weight { left: 195px; top: 716px; font-size: 30px; }
  .weight .estimated { font-family: "Arvo", serif; font-weight: 400; font-size: 40px; margin-left: 6px; vertical-align: -3px; }
  .storage { left: 195px; top: 758px; font-size: 15px; letter-spacing: 0.1px; }
  .description { left: 440px; top: 716px; font-size: 30px; line-height: 40px; letter-spacing: 0.3px; }
</style>
</head>
<body>
<main class="label">
  <div class="rule rule--v" style="left:507px; top:48px; height:409px;"></div>
  <div class="rule rule--h" style="left:46px; top:123px; width:463px;"></div>
  <div class="rule rule--h" style="left:42px; top:456px; width:1115px;"></div>
  <div class="rule rule--v" style="left:407px; top:456px; height:341px;"></div>
  <div class="rule rule--h" style="left:407px; top:541px; width:750px;"></div>
  <div class="rule rule--h" style="left:42px; top:688px; width:1115px;"></div>
  <div class="rule rule--v" style="left:160px; top:688px; height:109px;"></div>

  <p class="text company">HALVERN FIELDS CORPORATION</p>

  <h1 class="brand-name"><span>PAUL</span><span>DENTON</span></h1>

  <div class="hero-art" role="img" aria-label="Illustration of a steaming sausage in a bun with a zigzag of sauce"></div>

  <div class="map-art" role="img" aria-label="Map of Canada"></div>
  <p class="text script origin">100%<br>&nbsp;Canadian</p>

  <p class="text script natural">All Natural</p>

  <h2 class="text flavour">MUTTON &amp; MINT</h2>
  <p class="text product">PORK SAUSAGES</p>

  <p class="text count">X6</p>
  <p class="text weight">400G<span class="estimated">℮</span></p>
  <p class="text storage">KEEP REFRIGERATED</p>

  <p class="text description">6 MATURE MUTTON&nbsp; SAUSAGE,<br>INFUSED WITH MINT.</p>
</main>
</body>
</html>
```